web page design with coding

We are a start up insurance agency who needs to design a full functional web page. we recently did a postcard design though drawkettle I will upload the final project for you to see the color scheme/font we would like to continue to use. I also have a rough draft of verbage I would like our website to have. I will upload that as well.

Reason: I am sorry but the person who will make the final decision on the website is out of the country at the moment and will make the final decision when he returns.

Industry/Entity Type

Insurance

Coding

Coded - Design and coding required

```html
<!DOCTYPE html>
<html lang="en">
<head>
<meta charset="utf-8">
<title>Corvane Insurance Group</title>
<link rel="stylesheet" href="https://fonts.googleapis.com/css2?family=Libre+Baskerville:wght@400;700&family=Open+Sans:ital,wght@0,400;0,600;0,700;1,400&display=swap">
<style>
:root{
  --green:#2f7f45;
  --green-band:#2e8047;
  --navy:#1d3b6c;
  --ink:#333;
  --muted:#555;
  --light-band:#ebebeb;
  --footer:#2e2e2e;
  --footer-text:#d8d8d8;
  --tweet-bg:#3a3a3a;
  --white:#fff;
}
*{box-sizing:border-box;margin:0;padding:0}
html,body{width:1200px;height:2356px;overflow:hidden;background:var(--white)}
body{position:relative;font-family:"Open Sans",Arial,sans-serif;color:var(--ink)}
.abs{position:absolute}

/* header */
.brand{left:100px;top:19px;width:167px;height:102px;display:flex;align-items:center;gap:10px}
.brand-mark{width:14px;height:14px;background:var(--navy);flex:none}
.brand-name{font-family:"Libre Baskerville",Georgia,serif;font-weight:400;color:var(--navy);font-size:17px;line-height:1.25}
.top-contact{top:28px;display:flex;align-items:center;gap:12px;font-size:14px;color:var(--navy)}
.icon-ring{width:30px;height:30px;border:1.5px solid var(--green);border-radius:50%;display:flex;align-items:center;justify-content:center}
.nav{top:76px;left:612px;display:flex;font-family:"Libre Baskerville",Georgia,serif;font-size:13px;color:#222}
.nav a{color:inherit;text-decoration:none;margin-right:42px;padding-bottom:6px}
.nav a.active{color:var(--green);border-bottom:2px solid var(--green)}
.search{left:1087px;top:80px}

/* hero */
.hero{left:0;top:138px;width:1200px;height:550px;background:linear-gradient(160deg,#8e97a3 0%,#c9cdd2 35%,#e9e9ea 60%,#b8b6b2 100%)}
.hero-caption{left:272px;top:489px;width:644px;height:80px;background:linear-gradient(90deg,rgba(40,40,40,.45) 0%,rgba(40,40,40,.78) 12%,rgba(40,40,40,.78) 88%,rgba(40,40,40,.45) 100%);color:var(--white);font-family:"Libre Baskerville",Georgia,serif;font-size:28px;display:flex;align-items:center;justify-content:center}
.dots{left:580px;top:620px;display:flex;gap:10px}
.dots span{width:8px;height:8px;border-radius:50%;background:#9a9a9a}
.dots span.on{background:var(--green)}

/* welcome */
.welcome-title{left:0;width:1200px;top:744px;text-align:center;font-family:"Libre Baskerville",Georgia,serif;font-weight:700;font-size:28px;color:var(--navy)}
.welcome-title em{font-style:normal;color:var(--green)}
.welcome-text{left:150px;width:900px;top:793px;text-align:center;font-size:12.5px;line-height:23px;color:var(--ink)}
.circle{width:188px;height:188px;border-radius:50%;border:4px solid #e6e6e6;box-shadow:0 0 0 1px #ccc;display:flex;align-items:center;justify-content:center;color:var(--white);font-weight:600;font-size:13px}
.circle.business{left:371px;top:863px;background:radial-gradient(circle at 50% 40%,#5a6778,#2b3240)}
.circle.personal{left:638px;top:863px;background:radial-gradient(circle at 50% 40%,#b59a82,#6f5a4c)}

/* about */
.about{left:0;top:1095px;width:1200px;height:447px;background:var(--green-band)}
.about-title{left:100px;top:1146px;font-family:"Libre Baskerville",Georgia,serif;font-weight:700;font-size:29px;color:var(--white)}
.about-text{left:100px;top:1192px;width:495px;font-size:12px;line-height:22.5px;color:var(--white)}
.about-text p{margin-bottom:22.5px}
.btn{background:var(--navy);color:var(--white);font-size:14px;display:flex;align-items:center;justify-content:center;text-transform:uppercase}
.about-btn{left:100px;top:1421px;width:121px;height:41px}
.about-photo{left:624px;top:1150px;width:477px;height:331px;border:2px solid var(--white);background:linear-gradient(120deg,#eef1f4 0%,#b8c0cb 45%,#34415a 100%)}

/* agents */
.agent-photo{left:182px;top:1591px;width:167px;height:286px;background:linear-gradient(180deg,#f4f4f4 0%,#cdd9e8 55%,#9fb6d4 100%)}
.agent-title{left:451px;top:1606px;font-family:"Libre Baskerville",Georgia,serif;font-weight:700;font-size:28px;color:var(--navy)}
.agent-title em{font-style:normal;color:var(--green)}
.agent-text{left:451px;top:1671px;width:590px;font-size:12px;line-height:22px;color:var(--muted)}
.agent-btn{left:451px;top:1817px;width:119px;height:41px}

/* testimonial */
.quote-band{left:0;top:1952px;width:1200px;height:139px;background:var(--light-band)}
.avatar{left:567px;top:1921px;width:62px;height:62px;border-radius:50%;border:3px solid var(--white);background:linear-gradient(180deg,#6b7280,#1f2530)}
.quote{left:190px;width:820px;top:1998px;text-align:center;font-style:italic;font-size:12px;line-height:22px;color:var(--muted)}
.quote-name{left:0;width:1200px;top:2059px;text-align:center;font-size:13px;color:var(--green)}
.arrow{top:2009px}

/* footer */
.footer{left:0;top:2091px;width:1200px;height:265px;background:var(--footer)}
.f-title{top:2116px;font-weight:700;font-size:15px;color:var(--white)}
.f-list{font-size:11.5px;color:var(--footer-text);list-style:none}
.contact-list{left:103px;top:2154px}
.contact-list li{display:flex;align-items:center;gap:15px;line-height:16px}
.contact-list li.addr{align-items:flex-start}
.contact-list li.addr svg{margin-top:1px}
.contact-list .ico{width:12px;flex:none;display:flex;justify-content:center}
.services-list{left:383px;top:2149px}
.services-list li{display:flex;align-items:center;gap:8px;height:25.5px}
.tweet{left:619px;top:2152px;width:226px;height:119px;background:var(--tweet-bg);padding:10px 14px 0;font-size:11.5px;line-height:20.5px;color:var(--footer-text)}
.tweet .dot{display:inline-block;width:12px;height:12px;border-radius:50%;background:#9fd0ee;margin:0 10px 0 10px;vertical-align:-1px}
.tweet .more{position:absolute;right:12px;bottom:6px;text-decoration:underline;color:var(--white);font-size:11.5px}
.f-brand{left:900px;top:2146px;width:195px;height:119px;background:#e9e9ea;border:3px solid #bdbdbd;display:flex;align-items:center;justify-content:center;text-align:center;font-family:"Libre Baskerville",Georgia,serif;font-size:19px;line-height:1.3;color:var(--navy)}
.f-rule{left:0;top:2300px;width:1200px;height:1px;background:#3a3a3a}
.copyright{left:0;width:1200px;top:2316px;text-align:center;font-size:12px;color:var(--footer-text)}
</style>
</head>
<body>

<header>
  <div class="abs brand"><span class="brand-mark"></span><span class="brand-name">Corvane<br>Insurance<br>Group</span></div>
  <div class="abs top-contact" style="left:730px">
    <span class="icon-ring"><svg width="14" height="14" viewBox="0 0 24 24"><path fill="#2f7f45" d="M6.6 10.8a15 15 0 0 0 6.6 6.6l2.2-2.2c.3-.3.7-.4 1-.2 1.1.4 2.3.6 3.6.6.6 0 1 .4 1 1V20c0 .6-.4 1-1 1A17 17 0 0 1 3 4c0-.6.4-1 1-1h3.5c.6 0 1 .4 1 1 0 1.3.2 2.5.6 3.6.1.3 0 .7-.2 1z"/></svg></span>
    <span>(305)-555-0142</span>
  </div>
  <div class="abs top-contact" style="left:885px;top:26px">
    <span class="icon-ring" style="background:var(--green);border-color:var(--green)"><svg width="14" height="12" viewBox="0 0 24 20"><path fill="#fff" d="M0 2h24v16H0z"/><path fill="#2f7f45" d="M2 3.5l10 7 10-7v1.5l-10 7-10-7z"/></svg></span>
    <span>hello@corvanecover.com</span>
  </div>
  <nav class="abs nav">
    <a class="active">Home</a><a>Aboutus</a><a>Services</a><a>Agents</a><a>Contacts</a>
  </nav>
  <svg class="abs search" width="14" height="14" viewBox="0 0 20 20"><circle cx="8" cy="8" r="6" fill="none" stroke="#222" stroke-width="2.5"/><path d="M12.5 12.5L18 18" stroke="#222" stroke-width="2.8"/></svg>
</header>

<section>
  <div class="abs hero" role="img" aria-label="Photo of two people signing an insurance contract at a desk"></div>
  <div class="abs hero-caption">Protecting Your Business is Our Priority.</div>
  <div class="abs dots"><span></span><span class="on"></span><span></span></div>
</section>

<section>
  <h1 class="abs welcome-title"><em>WELCOME TO</em> CORVANE INSURANCE GROUP</h1>
  <p class="abs welcome-text">Corvane Insurance Group has joined with regional &amp; national insurance companies to provide quality products and superior service. We take the time to discuss<br>options and coverages, not to just sell insurance products. We strive to educate you in the decision making process to become an informed consumer.</p>
  <div class="abs circle business" role="img" aria-label="Photo of two businessmen reviewing documents">BUSINESS INSURANCE</div>
  <div class="abs circle personal" role="img" aria-label="Photo of a smiling family">PERSONAL INSURANCE</div>
</section>

<section>
  <div class="abs about" role="img" aria-label="Faded photo of a house behind a green overlay"></div>
  <h2 class="abs about-title">ABOUT US</h2>
  <div class="abs about-text">
    <p>Established in 2015, Corvane Insurance Group is a full service independent insurance agency. Our licensed agents have the experience to custom tailor a program to meet your specific needs &amp; our professional support staff will provide you with top notch customer service to help ease the burden of managing your insurance program.</p>
    <p>We have established relationships with carriers in order to offer you the most competitive products and services available in the marketplace today.</p>
    <p>We look forward to working with you!</p>
  </div>
  <div class="abs btn about-btn">View More</div>
  <div class="abs about-photo" role="img" aria-label="Photo of two smiling businessmen looking at a tablet"></div>
</section>

<section>
  <div class="abs agent-photo" role="img" aria-label="Photo of a smiling agent with arms crossed"></div>
  <h2 class="abs agent-title"><em>AGENTS</em> BIO</h2>
  <p class="abs agent-text">Evan's Bio to include education and insurance experience with info regarding any professional member-<br>ships etc.<br>Lorem Ipsum is simply dummy text of the printing and typesetting industry. Lorem Ipsum has been the industry's standard dummy text ever since the 1500s, when an unknown printer took a galley of type and scrambled it to make a type specimen book. It has survived not only five centuries.</p>
  <div class="abs btn agent-btn">View Profile</div>
</section>

<section>
  <div class="abs quote-band"></div>
  <div class="abs avatar" role="img" aria-label="Portrait of the client giving the testimonial"></div>
  <svg class="abs arrow" style="left:126px" width="14" height="26" viewBox="0 0 14 26"><path d="M12 2L2 13l10 11" fill="none" stroke="#aaa" stroke-width="2"/></svg>
  <svg class="abs arrow" style="left:1058px" width="14" height="26" viewBox="0 0 14 26"><path d="M2 2l10 11L2 24" fill="none" stroke="#aaa" stroke-width="2"/></svg>
  <p class="abs quote">“ Nemo enim ipsam voluptatem quia voluptas sit aspernatur aut odit aut fugit, sed quia consequuntur magni dolores eos qui ratione voluptatem sequi nesciunt. Neque porro quisquam est, qui dolorem ipsum quia dolor sit amet, consectetur, adipisci velit, sed quia non numquam eius ”</p>
  <p class="abs quote-name">- DANIEL MARSH</p>
</section>

<footer>
  <div class="abs footer"></div>
  <h3 class="abs f-title" style="left:99px">Contact Us</h3>
  <ul class="abs f-list contact-list">
    <li class="addr"><span class="ico"><svg width="10" height="14" viewBox="0 0 10 14"><path d="M5 0a5 5 0 0 0-5 5c0 4 5 9 5 9s5-5 5-9a5 5 0 0 0-5-5zm0 7a2 2 0 1 1 0-4 2 2 0 0 1 0 4z" fill="#fff"/></svg></span><span>4870 Alder Crest Way, Ste 200<br>Maple Falls, CA</span></li>
    <li style="margin-top:10px"><span class="ico"><svg width="12" height="12" viewBox="0 0 24 24"><path fill="#fff" d="M6.6 10.8a15 15 0 0 0 6.6 6.6l2.2-2.2c.3-.3.7-.4 1-.2 1.1.4 2.3.6 3.6.6.6 0 1 .4 1 1V20c0 .6-.4 1-1 1A17 17 0 0 1 3 4c0-.6.4-1 1-1h3.5c.6 0 1 .4 1 1 0 1.3.2 2.5.6 3.6.1.3 0 .7-.2 1z"/></svg></span><span>949.555.0178</span></li>
    <li style="margin-top:14px"><span class="ico"><svg width="9" height="14" viewBox="0 0 8 14"><rect x="1" y="0.5" width="6" height="13" rx="1" fill="none" stroke="#fff" stroke-width="1.3"/><rect x="3" y="11" width="2" height="1" fill="#fff"/></svg></span><span>07700 900 314</span></li>
    <li style="margin-top:5px;line-height:18px"><span class="ico"><svg width="14" height="12" viewBox="0 0 24 20"><path fill="#fff" d="M0 2h24v16H0z"/><path fill="#2e2e2e" d="M2 3.5l10 7 10-7v1.5l-10 7-10-7z"/></svg></span><span style="font-size:14px">hello@corvanecover.com</span></li>
  </ul>

  <h3 class="abs f-title" style="left:383px;font-weight:600;font-size:16px">Services</h3>
  <ul class="abs f-list services-list">
    <li><svg width="11" height="11" viewBox="0 0 12 12"><path d="M1 6l3.5 3.5L11 2" fill="none" stroke="#ddd" stroke-width="2"/></svg>Crime</li>
    <li><svg width="11" height="11" viewBox="0 0 12 12"><path d="M1 6l3.5 3.5L11 2" fill="none" stroke="#ddd" stroke-width="2"/></svg>Crop / Hail</li>
    <li><svg width="11" height="11" viewBox="0 0 12 12"><path d="M1 6l3.5 3.5L11 2" fill="none" stroke="#ddd" stroke-width="2"/></svg>Difference in Conditions</li>
    <li><svg width="11" height="11" viewBox="0 0 12 12"><path d="M1 6l3.5 3.5L11 2" fill="none" stroke="#ddd" stroke-width="2"/></svg>Directors and Officers (D&amp;O)</li>
    <li><svg width="11" height="11" viewBox="0 0 12 12"><path d="M1 6l3.5 3.5L11 2" fill="none" stroke="#ddd" stroke-width="2"/></svg>Employment Practices Liability</li>
  </ul>

  <h3 class="abs f-title" style="left:619px">Latest Tweets</h3>
  <div class="abs tweet"><span class="dot"></span>Check out - Responsive<br>Fernpage Blogging Theme' on<br>#Lorem Ipsum brookline<br>@Fenlow Studio<span class="more">show Summary</span></div>

  <div class="abs f-brand">Corvane<br>Insurance Group</div>
  <div class="abs f-rule"></div>
  <p class="abs copyright">Copyright © 2016, CIG | All Rights Reserved.</p>
</footer>

</body>
</html>
```